Commercial Rooftop Solar business needs a website

We need a website with fantastic appeal for a new company based in Melbourne called Tallow Ridge Energy. We design and install solar energy systems for commercial applications across Australia. Our market is to focus on small to medium businesses looking for solar solutions, but we will also provide our service for residential customers. We would like a beautiful 'front page' feel to our home page, using photographs of solar PV systems and/or natural imagery. Our logo uses the colours orange and black, which could easily be echoed in photographic imagery of sunset and sunrise, for example. The design should communicate quiet confidence and professionalism to a corporate marketplace.

NEW POINTS FOR BRIEF: This design also needs to be flexible to allow for additional future content, including a Support page with sub pages, FAQ's, and a Blog.

As part of this design project, we will require the coding for the website to be completed by the designer.

We have seen some websites, which we like the look and feel of: these are listed below.

brightvanepower.com.au:

• Beautiful images underlaying brief text selling points.
• Simple ‘front cover’ style home page with elegant drop-down menu, stylish simple font style.
• Home page invites exploration through the menu links, rather than trying to provide all the information up front.
• Company logo and name in the top left hand corner, contact details accessible at top right hand, seems consistent in most sites.

kelpworks.com.au

rumbofield.com:
• Same element as the others is the front-page style home page with beautiful images underlying text.

We have a webpage that we started uploading content to. You can use some of the content there in your designs: www.tallowridgeenergy.com.au

Technical Specifications:
PAGES:

Home

About Us

Solutions - Commercial
- Residential

Products - Solar Panels - Vorla Heron, Vorla TELD, Vorla QB
- Solar Inverters - Kestamo, BrilQuill
- Monitoring systems - Dunmere Metrics
- Batteries - RW

- Datasheets have been provided for reference but if it's too much work, you can use generic text and we will provide content later.

Contact Us

FUTURE PAGES (Please consider in structure, where links could be placed):

Support

FAQ's

Blog.

We could provide some content for the Support page soon, but the Blog and FAQ's are future pages which we don't want highlighted in the design as we don't yet have content.

Phone: 1800 7 BIRCH
Email: sales@tallowridgeenergy.com.au

Currently, I do not have images and text available. Please
use placeholders in the meantime. The final text and images will be uploaded for the winner once a winning design has been selected.

Target Market(s)

Primary focus is on small to medium sized business owners. Those owners will have a house which may be suitable for solar so we want to cater to residential deeper in the website.

Industry/Entity Type

Solar Energy

Coding

Coded - Design and coding required

Number of Pages Required

5+ page

Colors
f78f20
0255a3

Requirements
Must have
• Logo as per attachments.
Nice to have
• Logo can have alternate colours Eg. White on Orange or Black etc. provided colour correct logo is shown somewhere eg. footer or contact page.
• In the active site, I'd like to have:
• Very slowly zooming images - barely perceptible.
• Title text that rolls into place
• Subtle movements
• See https://plumtally.com.au/ for example

```html
<!DOCTYPE html>
<html lang="en">
<head>
<meta charset="utf-8">
<title>Contact Us – Tallow Ridge Energy</title>
<link rel="stylesheet" href="https://fonts.googleapis.com/css2?family=Josefin+Sans:wght@700&family=Lato:wght@400;700&family=Michroma&display=swap">
<style>
:root{
  --accent:#f73a0c;
  --ink:#1d1d1d;
  --body:#3a3a3a;
  --muted:#555;
  --line:#cfcfcf;
  --footer:#1c1c1c;
  --footer-deep:#121212;
  --white:#fff;
}
*{box-sizing:border-box;margin:0;padding:0}
html,body{width:1047px;height:1200px;overflow:hidden;background:var(--white)}
body{position:relative;font-family:"Lato",sans-serif;color:var(--body)}
.abs{position:absolute}

/* Hero */
.hero{left:0;top:0;width:1047px;height:397px;
  background:linear-gradient(180deg,#4d5560 0%,#7a6f68 22%,#c9713c 42%,#e5883d 50%,#7a4a36 62%,#3a3544 78%,#2a2d3c 100%)}
.brand{left:142px;top:40px;font-family:"Josefin Sans",sans-serif;font-weight:700;font-size:19px;color:var(--white);letter-spacing:.5px}
.brand-dot{display:inline-block;width:10px;height:10px;border-radius:50%;background:var(--white);margin-right:8px;vertical-align:1px}
.top-phone{left:644px;top:18px;display:flex;align-items:center;gap:8px;color:var(--white);font-weight:700;font-size:15px}
.estimate{left:784px;top:18px;width:131px;height:26px;border:1.5px solid var(--white);border-radius:14px;background:var(--accent);color:var(--white);font-size:11px;font-weight:700;display:flex;align-items:center;justify-content:center;gap:8px}
.nav{top:72px;font-family:"Michroma",sans-serif;font-size:10px;letter-spacing:1.6px;color:var(--white)}
.nav.active{color:var(--accent)}
.hero-title{left:200px;top:204px;width:647px;text-align:center;font-family:"Josefin Sans",sans-serif;font-weight:700;font-size:24.5px;line-height:31px;color:var(--white)}

/* Section heading */
.section-title{left:0;top:437px;width:1047px;text-align:center;font-family:"Michroma",sans-serif;font-size:23px;letter-spacing:2px;color:var(--ink);font-variant:small-caps}
.rule{height:1.5px;background:var(--ink)}
.intro{left:160px;top:524px;width:727px;text-align:center;font-size:12.3px;line-height:19.5px;color:var(--body)}

.col-title{top:596px;font-family:"Michroma",sans-serif;font-size:18px;letter-spacing:2px;color:var(--ink);font-variant:small-caps}
.field{left:151px;width:331px;height:33px;border:1px solid var(--line);padding:0 10px;font-size:11px;color:var(--muted);display:flex;align-items:center;justify-content:space-between}
.field.area{align-items:flex-start;padding-top:12px}
.btn{background:var(--accent);color:var(--white);border-radius:13px;font-family:"Michroma",sans-serif;font-variant:small-caps;letter-spacing:1.3px;display:flex;align-items:center;justify-content:center}
.divider{left:518px;top:595px;width:1px;height:335px;background:#e4e4e4}

.map{left:543px;top:640px;width:361px;height:145px;border:1px solid #bbb;background:linear-gradient(135deg,#93b9e6 0%,#e9e4d6 45%,#efe9da 60%,#8fb4e0 100%)}
.info-icon{left:543px;width:26px;height:26px;border:1px solid #ccc;border-radius:50%;display:flex;align-items:center;justify-content:center}
.info-label{left:578px;font-size:11px;font-weight:700;color:var(--accent)}
.info-text{left:578px;font-size:10.5px;color:var(--body)}

/* Footer */
.footer{left:0;top:964px;width:1047px;height:199px;background:var(--footer)}
.footer-bar{left:0;top:1163px;width:1047px;height:37px;background:var(--footer-deep);color:#ddd;font-size:9px;text-align:center;line-height:37px}
.f-title{top:991px;font-family:"Michroma",sans-serif;font-variant:small-caps;font-size:11.5px;letter-spacing:1.6px;color:var(--white)}
.f-rule{top:1012px;height:0;border-top:1px dotted #666}
.f-sep{top:1005px;width:1px;height:130px;background:#2a2a2a}
.f-link{left:139px;font-size:10px;color:#eee}
.f-link::before{content:"›";color:#888;margin-right:6px}
.f-input{left:314px;width:166px;background:var(--white);border-radius:3px;font-size:8px;color:#555;padding:3px 6px}
.f-text{left:527px;color:#eee;font-size:10px}
.f-hr{left:527px;width:175px;height:1px;background:#2e2e2e}
.f-brand{left:760px;top:1060px;width:160px;text-align:center;font-family:"Josefin Sans",sans-serif;font-weight:700;font-size:16px;color:#b8b8b8}
</style>
</head>
<body>

<header>
  <div class="abs hero" role="img" aria-label="Sunset over rows of solar panels"></div>
  <div class="abs brand"><span class="brand-dot"></span>Tallow Ridge Energy</div>
  <div class="abs top-phone">
    <svg width="25" height="25" viewBox="0 0 25 25"><circle cx="12.5" cy="12.5" r="11.5" fill="none" stroke="#fff" stroke-width="1.5"/><path d="M9 7.5l2 0 1 3-1.5 1a7 7 0 0 0 3 3l1-1.5 3 1v2c0 1-1 1.5-2 1.3C11 16.5 8.5 14 7.8 9.5 7.6 8.5 8 7.5 9 7.5z" fill="#fff"/></svg>
    1800 7 BIRCH
  </div>
  <div class="abs estimate">FREE ESTIMATE
    <svg width="16" height="17" viewBox="0 0 16 17"><rect x="2" y="1" width="10" height="14" fill="none" stroke="#fff" stroke-width="1.2"/><path d="M4.5 10h5M4.5 12.5h4M14 7l-5 6" stroke="#fff" stroke-width="1.2"/></svg>
  </div>
  <nav>
    <span class="abs nav" style="left:497px">HOME</span>
    <span class="abs nav" style="left:581px">ABOUT US</span>
    <span class="abs nav" style="left:698px">SOLUTIONS</span>
    <span class="abs nav active" style="left:825px">CONTACT US</span>
  </nav>
  <h1 class="abs hero-title">Tallow Ridge Energy Is A National Company That Specialises In Solar Solutions For The Commercial And Residential</h1>
</header>

<main>
  <div class="abs rule" style="left:348px;top:455px;width:70px"></div>
  <h2 class="abs section-title">Contact Us</h2>
  <div class="abs rule" style="left:632px;top:455px;width:67px"></div>
  <p class="abs intro">Lorem ipsum dolor sit amet, consectetuer adipiscing elit, sed diam nonummy nibh euismod tincidunt ut laoreet dolore magna aliquam erat volutpat ut wisi enim ad minim veniam, quis nostrud exerci tation ullamcorper suscipit lobortis nisl ut aliquip ex ea commodo consequat.</p>

  <section class="inquiry">
    <h3 class="abs col-title" style="left:154px">Quick Inquiry</h3>
    <div class="abs field" style="top:640px">Name *</div>
    <div class="abs field" style="top:682px">Email *</div>
    <div class="abs field" style="top:723px">Phone *</div>
    <div class="abs field" style="top:763px;height:32px">Solutions
      <svg width="10" height="6" viewBox="0 0 10 6"><path d="M1 1l4 4 4-4" fill="none" stroke="#444" stroke-width="1.2"/></svg>
    </div>
    <div class="abs field area" style="top:805px;height:85px">Description of Business</div>
    <div class="abs btn" style="left:151px;top:901px;width:79px;height:25px;font-size:11px">Submit</div>
  </section>

  <div class="abs divider"></div>

  <section class="location">
    <h3 class="abs col-title" style="left:549px">Location Map</h3>
    <div class="abs map" role="img" aria-label="Street map showing the office location"></div>

    <div class="abs info-icon" style="top:809px">
      <svg width="10" height="13" viewBox="0 0 10 13"><path d="M5 0a5 5 0 0 1 5 5c0 3.5-5 8-5 8S0 8.5 0 5a5 5 0 0 1 5-5z" fill="#f73a0c"/><circle cx="5" cy="5" r="1.8" fill="#fff"/></svg>
    </div>
    <div class="abs info-label" style="top:808px">TALLOW RIDGE ENERGY</div>
    <div class="abs info-text" style="top:822px">123 euismod cidun ut aoreetmok laoreet dol magnak aliquam</div>

    <div class="abs info-icon" style="top:849px">
      <svg width="12" height="12" viewBox="0 0 12 12"><path d="M2 0.5l2.5 0 1 3-1.5 1.2a7 7 0 0 0 3.3 3.3L8.5 6.5l3 1v2.5c0 1-1 1.5-2 1.3C5 10.5 1.5 7 0.6 2.5 0.4 1.3 1 .5 2 .5z" fill="#f73a0c"/></svg>
    </div>
    <div class="abs info-label" style="top:848px">PHONE</div>
    <div class="abs info-text" style="top:862px;font-weight:700">1800 7 BIRCH</div>

    <div class="abs info-icon" style="top:890px">
      <svg width="12" height="9" viewBox="0 0 12 9"><rect width="12" height="9" rx="1" fill="#f73a0c"/><path d="M0.5 1l5.5 4 5.5-4" fill="none" stroke="#fff" stroke-width="1"/></svg>
    </div>
    <div class="abs info-label" style="top:889px">EMAIL</div>
    <div class="abs info-text" style="top:903px">info@tallowridgeenergy.com.au</div>
  </section>
</main>

<footer>
  <div class="abs footer"></div>
  <div class="abs f-sep" style="left:275px"></div>
  <div class="abs f-sep" style="left:501px"></div>
  <div class="abs f-sep" style="left:741px"></div>

  <h4 class="abs f-title" style="left:140px">Quick Links</h4>
  <div class="abs f-rule" style="left:140px;width:92px"></div>
  <span class="abs f-link" style="top:1024px">Home</span>
  <span class="abs f-link" style="top:1052px">About Us</span>
  <span class="abs f-link" style="top:1080px">Solutions</span>
  <span class="abs f-link" style="top:1108px">Contact Us</span>

  <h4 class="abs f-title" style="left:314px">Quick Inquiry</h4>
  <div class="abs f-rule" style="left:314px;width:168px"></div>
  <div class="abs f-input" style="top:1024px;height:17px">Name</div>
  <div class="abs f-input" style="top:1046px;height:17px">Email</div>
  <div class="abs f-input" style="top:1068px;height:31px">Message</div>
  <div class="abs btn" style="left:314px;top:1104px;width:60px;height:20px;font-size:8px;border-radius:10px">Submit</div>

  <h4 class="abs f-title" style="left:527px">Contact Details</h4>
  <div class="abs f-rule" style="left:527px;width:175px"></div>
  <svg class="abs" style="left:528px;top:1024px" width="8" height="11" viewBox="0 0 10 13"><path d="M5 0a5 5 0 0 1 5 5c0 3.5-5 8-5 8S0 8.5 0 5a5 5 0 0 1 5-5z" fill="#f73a0c"/><circle cx="5" cy="5" r="1.8" fill="#1c1c1c"/></svg>
  <div class="abs f-text" style="left:544px;top:1021px;font-size:12px;font-weight:700">TALLOW RIDGE ENERGY</div>
  <div class="abs f-text" style="left:544px;top:1039px;line-height:13px;width:160px">123 euismod cidun ut aoreetmok laoreet dol magnak aliquam</div>
  <div class="abs f-hr" style="top:1073px"></div>
  <svg class="abs" style="left:527px;top:1082px" width="10" height="10" viewBox="0 0 12 12"><path d="M2 0.5l2.5 0 1 3-1.5 1.2a7 7 0 0 0 3.3 3.3L8.5 6.5l3 1v2.5c0 1-1 1.5-2 1.3C5 10.5 1.5 7 0.6 2.5 0.4 1.3 1 .5 2 .5z" fill="#f73a0c"/></svg>
  <div class="abs f-text" style="left:543px;top:1080px">1800 7 BIRCH</div>
  <div class="abs f-hr" style="top:1101px"></div>
  <svg class="abs" style="left:526px;top:1111px" width="11" height="8" viewBox="0 0 12 9"><rect width="12" height="9" rx="1" fill="#f73a0c"/><path d="M0.5 1l5.5 4 5.5-4" fill="none" stroke="#1c1c1c" stroke-width="1"/></svg>
  <div class="abs f-text" style="left:543px;top:1108px;font-size:10.5px">info@tallowridgeenergy.com.au</div>

  <div class="abs f-brand">Tallow Ridge Energy</div>

  <div class="abs footer-bar">Copyright © 2017 Tallow Ridge Energy. All Right Reserved.</div>
</footer>

</body>
</html>
```